Small legal and financial translation company needs Squarespace website, brochure and logo

Hello,
We are Lumarin Services (www.lumarinservices-example.com), a boutique legal and financial translation company. We offer our services mainly to Spanish customers. Our primary line of business is the translation of financial statements, but we translate a wide variety legal and financial texts.
The project we are offering comprises three parts: a redo of the current website, an informational brochure for potential customer and a logo design. These three parts should provide a consistent image. We would develop content soon.
We are looking for a website that would look like a typical law firm website, nothing too fancy. Right now, it is in English, Spanish and French, although the new site need only be in English and Spanish. There must be good toggling between the English and Spanish versions. There would be no need for tie-ins to social media and it would not contain a blog. Basically, a static site. We aren't interesting in driving traffic to the site or SEO, as we will contact nearly all potential customers beforehand. The website must be built in Squarespace to enable a smooth transition. The content would be similar to the current page, we'll be working on the exact content, but a rough draft is attached.
The brochure will be some three pages and would introduce the company to potential customers, using similar images as the website and the logo to be designed.
The only specifications for the logo is, as the website and brochure, it convey a sense of security and trust.
Feel free to ask with any questions as this is the first time we have used this platform.
Thank you!
Updates

I've added a more or less final version for the text in the brochure and updated the brief. Added Wednesday, June 10, 2015

Target Market(s)

Spanish law firms, auditors, accountants, banks, investment firms

Industry/Entity Type

Finance

Logo Text

Lumarin Services

Number of Pages Required

5+ page

Font styles to use
Serif

Requirements
Must have
• The website must be built in Squarespace and have a good option to toggle between English and Spanish versions.
• Brochure must be in both English and Spanish, I'm attaching a rough draft of the information that it will probably have. This should give an idea about what to include and the spacing. I will update it to include the final information.
Nice to have
• Would be nice to have some quality finance- and legal-related images
Should not have
• Vibrant colours

```html
<!DOCTYPE html>
<html lang="en">
<head>
<meta charset="UTF-8">
<title>Lumarin Services – Brochure Cover</title>
<link rel="stylesheet" href="https://fonts.googleapis.com/css2?family=Cinzel:wght@400&family=Cormorant+Garamond:wght@400;500&display=swap">
<style>
  :root {
    --backdrop: #cccccc;
    --paper: #ffffff;
    --navy: #2b437e;
    --ink: #000000;
    --photo-light: #e6e6e6;
    --photo-mid: #9a9a9a;
    --photo-dark: #2e2e2e;
    --type-light: #ffffff;
  }
  * { margin: 0; padding: 0; box-sizing: border-box; }
  html, body {
    width: 1200px; height: 1200px; overflow: hidden;
    background: var(--backdrop);
  }
  .brochure-cover {
    position: absolute; left: 268px; top: 110px;
    width: 700px; height: 990px;
    background: var(--paper);
    box-shadow: 0 4px 14px rgba(0,0,0,0.35);
    overflow: hidden;
  }
  .masthead {
    position: absolute; left: 0; top: 0; width: 700px; height: 153px;
    display: flex; align-items: center; justify-content: center; gap: 16px;
  }
  .brand-mark {
    width: 40px; height: 40px; background: var(--navy);
  }
  .brand-name {
    font-family: "Cinzel", "Times New Roman", serif;
    font-weight: 400; font-size: 40px; letter-spacing: 1px;
    color: var(--ink);
  }
  .masthead-rule {
    position: absolute; left: 3px; top: 153px; width: 697px; height: 5px;
    background: var(--navy);
  }
  .hero-photo {
    position: absolute; left: 0; top: 158px; width: 700px; height: 832px;
    background:
      radial-gradient(ellipse at 72% 40%, var(--photo-dark) 0%, transparent 45%),
      linear-gradient(160deg, var(--photo-light) 0%, var(--photo-mid) 45%, var(--photo-light) 80%);
  }
  .cover-shapes {
    position: absolute; left: 0; top: 0; width: 700px; height: 990px;
  }
  .web-address {
    position: absolute; left: 37px; top: 766px;
    font-family: "Cormorant Garamond", "Times New Roman", serif;
    font-size: 20px; color: var(--type-light);
  }
  .tagline {
    position: absolute; left: 250px; top: 824px; width: 455px;
    font-family: "Cormorant Garamond", "Times New Roman", serif;
    font-weight: 500; font-size: 29px; line-height: 37px;
    text-align: center; color: var(--type-light);
  }
</style>
</head>
<body>
  <main class="brochure-cover">
    <header class="masthead">
      <span class="brand-mark"></span>
      <span class="brand-name">LUMARIN SERVICES</span>
    </header>
    <div class="masthead-rule"></div>
    <div class="hero-photo" role="img" aria-label="Black and white photo of a lawyer signing documents at a desk beside a statue of Lady Justice"></div>
    <svg class="cover-shapes" viewBox="0 0 700 990" aria-hidden="true">
      <polygon points="0,712 76,588 347,760 0,985" fill="var(--navy)"/>
      <polygon points="627,588 700,540 700,712" fill="var(--navy)"/>
      <polygon points="0,987 627,588 700,712 700,990 0,990" fill="var(--ink)"/>
      <line x1="0" y1="986" x2="700" y2="540" stroke="var(--paper)" stroke-width="3"/>
      <line x1="627" y1="588" x2="700" y2="712" stroke="var(--paper)" stroke-width="2"/>
    </svg>
    <p class="web-address">www.lumarinservices-example.com</p>
    <p class="tagline">High-quality translation services<br>in English, Spanish and French<br>for legal and financial documents</p>
  </main>
</body>
</html>
```